Business Card Design Project

Business and Appointment Card for Medical Practice. On back of card we would like to have: blank line for patient name, Mon-Fri each with a check box next to the day, blank line for appointment date, blank line for appointment time, with option to circle am or pm.

Target Market(s)

Professional Business Associates, as well as function as patient appointment cards (on back side of card)

Industry/Entity Type

Business

Colors

Designer to choose colors to be used in the design.

```html
<!DOCTYPE html>
<html lang="en">
<head>
<meta charset="utf-8">
<title>Willow Brook Medical Associates – Appointment Card</title>
<link rel="stylesheet" href="https://fonts.googleapis.com/css2?family=Cinzel:wght@600&family=Questrial&display=swap">
<style>
  :root {
    --backdrop: #d9d9d9;
    --card: #ffffff;
    --red: #8b1c1f;
    --green: #1d6a38;
  }
  * { box-sizing: border-box; margin: 0; padding: 0; }
  html, body {
    width: 983px;
    height: 1200px;
    overflow: hidden;
    background: var(--backdrop);
  }
  .canvas {
    position: relative;
    width: 983px;
    height: 1200px;
  }
  .card {
    position: absolute;
    left: 128px;
    width: 726px;
    height: 424px;
    background: var(--card);
  }
  .card--back { top: 114px; }
  .card--front { top: 654px; }

  /* Appointment side */
  .field {
    position: absolute;
    font-family: "Questrial", sans-serif;
    font-size: 20px;
    color: var(--red);
    white-space: nowrap;
    display: flex;
    align-items: flex-end;
  }
  .field__line {
    display: inline-block;
    border-bottom: 1.5px solid var(--green);
    height: 1px;
    margin-left: 12px;
    margin-bottom: 4px;
  }
  .field--name { left: 44px; top: 106px; }
  .field--name .field__line { width: 464px; }
  .field--date { left: 42px; top: 182px; }
  .field--date .field__line { width: 193px; }
  .field--time { left: 42px; top: 249px; }
  .field--time .field__line { width: 104px; margin-left: 6px; margin-right: 8px; }
  .meridiem { margin-right: 6px; }
  .checkbox {
    display: inline-block;
    width: 15px;
    height: 15px;
    border: 1.5px solid var(--red);
    margin: 0 10px 3px 4px;
  }
  .rule {
    position: absolute;
    left: 0;
    top: 371px;
    width: 536px;
    border-top: 2px solid var(--red);
  }
  .mini-brand {
    position: absolute;
    left: 548px;
    top: 356px;
    width: 150px;
    text-align: center;
    font-family: "Cinzel", serif;
    font-weight: 600;
    color: var(--green);
    line-height: 1.1;
  }
  .mini-brand__name { display: block; font-size: 15px; }
  .mini-brand__sub { display: block; font-size: 9px; letter-spacing: 0.5px; }

  /* Business side */
  .brand {
    position: absolute;
    left: 0;
    right: 0;
    top: 52px;
    text-align: center;
    font-family: "Cinzel", serif;
    font-weight: 600;
    color: var(--green);
  }
  .brand__mark {
    display: block;
    margin: 0 auto 22px;
  }
  .brand__name {
    display: block;
    font-size: 56px;
    line-height: 1;
    letter-spacing: 1px;
  }
  .brand__sub {
    display: block;
    font-size: 28px;
    letter-spacing: 3px;
    margin-top: 8px;
  }
</style>
</head>
<body>
<main class="canvas">
  <section class="card card--back" aria-label="Appointment side">
    <div class="field field--name">Patient Name :<span class="field__line"></span></div>
    <div class="field field--date">Appointment Date :<span class="field__line"></span></div>
    <div class="field field--time">Time :<span class="field__line"></span>
      <span class="meridiem">a.m.</span><span class="checkbox"></span>
      <span class="meridiem">p.m.</span><span class="checkbox"></span>
    </div>
    <div class="rule"></div>
    <div class="mini-brand">
      <span class="mini-brand__name">Willow Brook</span>
      <span class="mini-brand__sub">Medical Associates</span>
    </div>
  </section>

  <section class="card card--front" aria-label="Business side">
    <div class="brand">
      <svg class="brand__mark" width="200" height="180" viewBox="0 0 200 180" aria-hidden="true">
        <circle cx="100" cy="90" r="84" fill="none" stroke="var(--green)" stroke-width="5"/>
      </svg>
      <span class="brand__name">Willow Brook</span>
      <span class="brand__sub">Medical Associates</span>
    </div>
  </section>
</main>
</body>
</html>
```